"Tovi's" Website Design

Tovi's makes earth friendly, healthy, and delicious snacks that are completely gluten free. We are looking for a website that is easy to navigate, energetic, and conveys our purpose "To create healthy, earth-friendly, gluten free snacks that fill bellies and warm hearts."
Our first product is "Tovi's Crunch Rockets" are a small, square, cracker pack with an unreasonable amount of cheddar cheese flavor. The flavor literally explodes in your mouth!
We really want our site to pop and show off some personality.
I'm attaching the logo for the company, feel free to go beyond the logo in terms of color.
Here are some sites that we like!
http://www.plumvaleco.com/company
http://www.mirtlefarm.com/
http://www.qv47.com/
http://www.dexterwalts.com/
http://www.hovrapack.com/food/products_zing/
http://www.perrinsfrostery.com/

```html
<!DOCTYPE html>
<html lang="en">
<head>
<meta charset="utf-8">
<title>Tovi's</title>
<link rel="stylesheet" href="https://fonts.googleapis.com/css2?family=Kalam:wght@400;700&family=Patrick+Hand&family=Arimo:wght@400&display=swap">
<style>
:root{
  --paper:#e7e7e7;
  --paper-dark:#dcdcdc;
  --orange:#f4652b;
  --rule:#9a9a9a;
  --grey-text:#9a9a9a;
  --ink:#222;
  --footer:#3b3b3b;
  --footer-edge:#262626;
  --footer-text:#d6d6d6;
  --frame:#c8a877;
  --white:#fff;
}
*{box-sizing:border-box;margin:0;padding:0}
html,body{width:1200px;height:867px;overflow:hidden}
body{position:relative;background:radial-gradient(circle at 40% 30%,var(--paper),var(--paper-dark));font-family:Arimo,Arial,sans-serif}
.abs{position:absolute}
.rule-h{left:85px;top:107px;width:1040px;height:3px;background:var(--rule);border-radius:2px;transform:rotate(-0.2deg)}
.rule-v{left:1105px;top:42px;width:3px;height:634px;background:var(--rule);border-radius:2px;transform:rotate(0.3deg)}
.rule-side{left:268px;top:129px;width:3px;height:542px;background:var(--rule);border-radius:2px}
.brand{left:78px;top:26px;font-family:Kalam,cursive;font-weight:700;font-size:46px;color:var(--orange);line-height:1}
.nav{left:425px;top:46px;display:flex;gap:18px;list-style:none}
.nav li{position:relative;font-family:Kalam,cursive;font-size:21px;color:var(--orange);padding-left:12px;line-height:1.3}
.nav li::before{content:"";position:absolute;left:0;top:2px;width:26px;height:26px;border-radius:50%;background:var(--white);z-index:-1}
.call{left:87px;top:130px;font-family:Arimo,sans-serif;font-size:16px;color:var(--orange)}
.social{left:102px;top:163px;display:flex;gap:12px}
.social span{width:42px;height:42px;border-radius:50%;background:var(--white);border:2px solid #c9c9c9}
.side-title{font-family:"Patrick Hand",cursive;font-size:23px;color:var(--ink)}
.side-list{list-style:none;font-size:14px;color:var(--grey-text);line-height:24px;margin-top:6px;padding-left:2px}
.flavor{left:95px;top:238px}
.category{left:95px;top:460px}
.hero-art{left:305px;top:125px;width:273px;height:246px;border-radius:40% 50% 45% 55%;background:radial-gradient(circle at 40% 40%,#c7965e,#8a6440 55%,#4f7fae 90%)}
.quote{left:605px;top:156px;width:465px;font-family:Kalam,cursive;font-size:22px;line-height:35px;color:var(--orange)}
.dots{left:975px;top:291px;display:flex;gap:5px}
.dots span{width:20px;height:20px;border-radius:50%;background:#b9b9b9}
.dots span.on{background:var(--orange)}
.divider{left:311px;top:379px;width:753px;height:5px;background:linear-gradient(90deg,#c4c4c4,#adadad,#c4c4c4);border-radius:3px}
.section-title{left:303px;top:397px;font-family:Kalam,cursive;font-weight:700;font-size:21px;letter-spacing:1px;color:var(--orange)}
.product{top:445px;width:154px}
.product .frame{width:154px;height:153px;background:var(--frame);border:2px solid #222;border-radius:10px 14px 8px 12px;padding:8px}
.product .photo{width:100%;height:100%;border-radius:6px}
.product dl{margin-top:16px;font-size:13px;color:#8a8a8a;line-height:22px}
.p1{left:311px}.p2{left:509px}.p3{left:706px}.p4{left:898px}
.p1 .photo{background:linear-gradient(160deg,#b89a70,#f0ead8 55%,#d9cbb0)}
.p2 .photo{background:linear-gradient(160deg,#8a6a52,#d58a4c 45%,#c9965f 80%)}
.p3 .photo{background:linear-gradient(160deg,#7a6a5a,#c9a070 45%,#e2c491 80%)}
.p4 .photo{background:linear-gradient(160deg,#c9602a,#b87845 50%,#5b3520)}
.product dl dd{display:none}
.footer{left:0;top:679px;width:1200px;height:188px;background:var(--footer);border-top:7px solid var(--footer-edge)}
.f-title{font-size:15px;color:var(--orange);top:26px}
.f-list{list-style:none;font-size:12px;color:var(--footer-text);line-height:23px;top:56px}
.contact{left:482px;top:56px;font-size:12px;color:var(--footer-text);line-height:23px}
.contact .indent{padding-left:54px}
.offers-text{left:785px;top:54px;width:270px;font-size:12px;line-height:17px;color:#b8b8b8}
.email{left:784px;top:96px;width:267px;height:34px;background:#5f5f5f;border:none}
.submit{left:971px;top:138px;width:80px;height:24px;border:2px solid #9a9a9a;background:transparent;color:#c9c9c9;font-size:15px;font-family:Arimo,sans-serif}
</style>
</head>
<body>
<header>
  <div class="abs brand">Tovi's</div>
  <ul class="abs nav">
    <li>Company</li><li>Our Products</li><li>Shop</li><li>Recipes &amp; Fun</li><li>Gift</li><li>Locations</li>
  </ul>
</header>
<div class="abs rule-h"></div>
<div class="abs rule-v"></div>
<div class="abs rule-side"></div>

<aside>
  <p class="abs call">Call Us : 0987 6543 210</p>
  <div class="abs social"><span></span><span></span><span></span></div>
  <section class="abs flavor">
    <h3 class="side-title">Shop by Flavor</h3>
    <ul class="side-list"><li>Lightly Salted</li><li>Barbeque</li><li>Dill Pickle</li><li>Sour Cream N Chive</li><li>Salt N Vinegar</li><li>Sour Cream N Chive</li><li>Salt N Vinegar</li></ul>
  </section>
  <section class="abs category">
    <h3 class="side-title">Shop by Category</h3>
    <ul class="side-list"><li>Lightly Salted</li><li>Barbeque</li><li>Dill Pickle</li><li>Sour Cream N Chive</li><li>Salt N Vinegar</li><li>Sour Cream N Chive</li><li>Salt N Vinegar</li></ul>
  </section>
</aside>

<main>
  <div class="abs hero-art" role="img" aria-label="Illustration of a towering stacked sandwich exploding with colourful fillings on a blue plate"></div>
  <p class="abs quote">Lorem ipsum dolor sit amet, consectetur adipisicing elit, sed do eiusmod tempor incididunt ut labore et dolore magna aliqua. Ut enim ad minim veniam, quis nostrud</p>
  <div class="abs dots"><span class="on"></span><span></span><span></span><span></span></div>
  <div class="abs divider"></div>
  <h2 class="abs section-title">OUR PRODUCTS</h2>
  <article class="abs product p1"><div class="frame"><div class="photo" role="img" aria-label="Photo of white crunchy cheese bites"></div></div><dl><dt>Name:</dt><dt>Description :</dt></dl></article>
  <article class="abs product p2"><div class="frame"><div class="photo" role="img" aria-label="Photo of a nut-coated cheese ball with crackers"></div></div><dl><dt>Name:</dt><dt>Description :</dt></dl></article>
  <article class="abs product p3"><div class="frame"><div class="photo" role="img" aria-label="Photo of a pecan cheese ball with crackers"></div></div><dl><dt>Name:</dt><dt>Description :</dt></dl></article>
  <article class="abs product p4"><div class="frame"><div class="photo" role="img" aria-label="Photo of golden cheese balls on a board"></div></div><dl><dt>Name:</dt><dt>Description :</dt></dl></article>
</main>

<footer class="abs footer">
  <h4 class="abs f-title" style="left:99px">Quick Links</h4>
  <ul class="abs f-list" style="left:101px"><li>Our Mision</li><li>Our People</li><li>Careers</li><li>Investor Relations</li><li>Press</li></ul>
  <ul class="abs f-list" style="left:284px"><li>Shop Online</li><li>Store Locator</li><li>Contact Us</li><li>FAQs</li><li>Privacy Policy</li></ul>
  <h4 class="abs f-title" style="left:478px">Contact Us</h4>
  <div class="abs contact">
    <p>Address :Lorem ipsum dolor sit amet,</p>
    <p class="indent">consectetur adipisicing elit,</p>
    <p>Phone no.:</p><p>Fax No.:</p><p>Email id:</p>
  </div>
  <h4 class="abs f-title" style="left:784px">Offers &amp; Promotions</h4>
  <p class="abs offers-text">Enter your email Id to get informations about opur offers &amp; promotions</p>
  <input class="abs email" type="text" aria-label="Email">
  <button class="abs submit">Submit</button>
</footer>
</body>
</html>
```